Keystone Polished Concrete & Grinding
I'm looking for a business card and logo design for my
new Polished Concrete & Grinding business,
If you were to look up Keystone in the dictionary it would
say, first in importance, order, or position; leading.
Polished Concrete floors are a niche market, that are being used currently in Shopping centres, office spaces and by most high end architects, builders and designers.
i need my business card & logo to stand out from my
competitors, i need my design + logo to reflect this it
needs to be simple, professional, eye catching, easy
to read and scream quality. The logo will need to be
suitable for a whole range of applications including,
uniforms, letter heads, stickers, and eventually
incorporating in vehicle vinyl wrapping.
Target Market(s)
Builders, architects, Interior designers & home owners
Contact Information for Business Card
Front side:
- Keystone Polished Concrete & Grinding.
- Logo
Rear side:
- Liam Varesko
- 0438175092
- info@keystonepcg-example.com.au
- commercial - domestic - industrial
- (later down the line website & space for
social media links
www.keystonepolishedslab-example.com.au)
Colors
Designer to choose colors to be used in the design.
Look and feel
Each slider illustrates characteristics of the customer's brand and the style your logo design should communicate.

```html
<!DOCTYPE html>
<html lang="en">
<head>
<meta charset="utf-8">
<title>Keystone Polished Concrete &amp; Grinding – Business Card</title>
<link href="https://fonts.googleapis.com/css2?family=Arimo:wght@400&family=Montserrat:wght@700&display=swap" rel="stylesheet">
<style>
  :root {
    --copper: #c27831;
    --steel: #a5b6c8;
    --paper: #ffffff;
    --ground: #e4e6e9;
    --ink-light: #ffffff;
    --card-w: 660px;
    --card-h: 377px;
  }
  * { box-sizing: border-box; margin: 0; padding: 0; }
  html, body { width: 1200px; height: 880px; overflow: hidden; }
  body {
    background: var(--ground);
    position: relative;
    font-family: "Arimo", Arial, sans-serif;
  }
  .card {
    position: absolute;
    width: var(--card-w);
    height: var(--card-h);
    background: var(--paper);
    border-radius: 26px;
    overflow: hidden;
    box-shadow: 0 10px 28px rgba(0,0,0,0.18);
  }
  .card--front { left: 170px; top: 38px; }
  .card--back  { left: 370px; top: 460px; }

  /* business name */
  .business-name {
    position: absolute;
    width: 420px;
    color: var(--copper);
    font-family: "Montserrat", Arial, sans-serif;
    font-weight: 700;
    font-size: 30px;
    line-height: 1.2;
  }
  .card--front .business-name { left: 120px; top: 150px; }
  .card--back .business-name { left: 100px; top: 64px; }

  /* back bands */
  .bands { position: absolute; inset: 0; width: 100%; height: 100%; }
  .holder-name {
    position: absolute;
    left: 52px; top: 236px;
    font-family: "Montserrat", Arial, sans-serif;
    font-weight: 700;
    font-size: 21px;
    color: var(--ink-light);
  }
  .contact-list {
    position: absolute;
    left: 40px; top: 300px;
    list-style: none;
    color: var(--ink-light);
    font-size: 14px;
  }
  .contact-list li { display: flex; align-items: center; gap: 8px; height: 22px; }
  .contact-list svg { width: 16px; height: 16px; flex: none; }
  .services {
    position: absolute;
    right: 36px; top: 250px;
    color: var(--ink-light);
    font-size: 14px;
  }
  .social {
    position: absolute;
    right: 36px; top: 278px;
    display: flex; gap: 8px;
  }
  .social span {
    width: 28px; height: 28px;
    border: 2px solid var(--ink-light);
    border-radius: 50%;
  }
</style>
</head>
<body>

  <section class="card card--front" aria-label="Card front">
    <p class="business-name">Keystone Polished Concrete &amp; Grinding</p>
  </section>

  <section class="card card--back" aria-label="Card back">
    <svg class="bands" viewBox="0 0 660 377" preserveAspectRatio="none" aria-hidden="true">
      <rect x="0" y="206" width="660" height="171" fill="var(--steel)"/>
      <path d="M0 288 L300 288 C322 288 326 278 326 262 C326 244 334 234 356 234 L660 234 L660 377 L0 377 Z" fill="var(--copper)"/>
    </svg>

    <p class="business-name">Keystone Polished Concrete &amp; Grinding</p>

    <p class="holder-name">Liam Varesko</p>

    <ul class="contact-list">
      <li>
        <svg viewBox="0 0 16 16" fill="none" stroke="#fff" stroke-width="1.3"><circle cx="8" cy="8" r="7.2"/><rect x="5.5" y="3.8" width="5" height="8.4" rx="1"/></svg>
        0438175092
      </li>
      <li>
        <svg viewBox="0 0 16 16" fill="none" stroke="#fff" stroke-width="1.3"><circle cx="8" cy="8" r="7.2"/><rect x="4" y="5.2" width="8" height="5.6"/><path d="M4 5.2 L8 8.5 L12 5.2"/></svg>
        info@keystonepcg-example.com.au
      </li>
      <li>
        <svg viewBox="0 0 16 16" fill="none" stroke="#fff" stroke-width="1.3"><circle cx="8" cy="8" r="7.2"/><circle cx="8" cy="8" r="4"/><path d="M4 8 H12 M8 4 V12"/></svg>
        www.keystonepolishedslab-example.com.au
      </li>
    </ul>

    <p class="services">Commercial | Domestic | Industrial</p>
    <div class="social" aria-label="Social media links">
      <span></span><span></span><span></span><span></span>
    </div>
  </section>

</body>
</html>
```